CREATE A BUSINESS CARD FOR A BOAT CLEANING SERVICE

WE ARE STARTING A NEW BOAT CLEANING BUSINESS. WE DIVE UNDERWATER TO CLEAN BOAT HULLS, JETTIES, UNDERWATER STRUCTURES ETC. WE ARE LOOKING FOR AN UPPERMARKET MODERN LOGO AND BUSINESS CARD AS ALOT OF OUR TARGET MARKET WILL BE HIGH END. YOU HAVE TO DESIGN A BUSINESS CARD AND LOGO SEPERATELY .
THE BUSINESS CARD DIMESNION MUST BE STANDARD SIZE.
The standard dimensions of a printed business card are 3.5 x 2 inches

Target Market(s)

UNDERWATER SERVICED

Industry/Entity Type

Business

Contact Information for Business Card

HOLLAND UNDERWATER SERVICES

Font styles to use
Serif

Colors

Designer to choose colors to be used in the design.

Requirements
Must have
• HOLLAND
Nice to have
• dark
Should not have
• more than 3 colors

```html
<!DOCTYPE html>
<html lang="en">
<head>
<meta charset="utf-8">
<title>Holland Underwater Services – Business Card</title>
<link rel="stylesheet" href="https://fonts.googleapis.com/css2?family=Oswald:wght@500&family=Oxygen:wght@400&display=swap">
<style>
  :root {
    --page-bg: #d3d3e0;
    --card-light: #f7f7f7;
    --card-mid: #e2e2e2;
    --card-dark: #a9a9ab;
    --ink: #111111;
    --accent: #2fb7df;
    --icon-ink: #ffffff;
  }
  * { margin: 0; padding: 0; box-sizing: border-box; }
  html, body {
    width: 1200px;
    height: 1006px;
    overflow: hidden;
    background: var(--page-bg);
  }
  .business-card {
    position: absolute;
    left: 100px;
    top: 217px;
    width: 1000px;
    height: 572px;
    background: linear-gradient(180deg, var(--card-light) 0%, var(--card-mid) 45%, var(--card-dark) 100%);
    box-shadow: 0 14px 30px rgba(60, 60, 80, 0.22);
    color: var(--ink);
    font-family: "Oxygen", sans-serif;
  }
  .brand {
    position: absolute;
    left: 158px;
    top: 70px;
    display: flex;
    align-items: center;
    gap: 22px;
  }
  .brand-mark {
    width: 118px;
    height: 118px;
    border-radius: 50%;
    background: var(--accent);
    flex: none;
  }
  .brand-name {
    font-family: "Oswald", sans-serif;
    font-weight: 500;
    color: var(--ink);
    line-height: 1;
  }
  .brand-name .primary {
    display: block;
    font-size: 104px;
    letter-spacing: 1px;
  }
  .brand-name .secondary {
    display: block;
    font-size: 27px;
    letter-spacing: 1px;
    margin-top: 6px;
  }
  .person {
    position: absolute;
    right: 548px;
    top: 382px;
    text-align: right;
  }
  .person-name {
    font-size: 34px;
    line-height: 1.1;
  }
  .person-role {
    font-size: 23px;
    margin-right: -2px;
  }
  .divider {
    position: absolute;
    left: 482px;
    top: 290px;
    width: 2px;
    height: 218px;
    background: var(--ink);
  }
  .contact-list {
    position: absolute;
    left: 512px;
    top: 292px;
    list-style: none;
  }
  .contact-list li {
    display: flex;
    align-items: center;
    gap: 12px;
    font-size: 26px;
    height: 41px;
  }
  .contact-icon {
    width: 20px;
    height: 20px;
    flex: none;
  }
</style>
</head>
<body>
  <main class="business-card">
    <div class="brand">
      <div class="brand-mark" aria-hidden="true"></div>
      <div class="brand-name">
        <span class="primary">HOLLAND</span>
        <span class="secondary">UNDERWATER SERVICES</span>
      </div>
    </div>

    <div class="person">
      <p class="person-name">Mark Ellison</p>
      <p class="person-role">Service Manager</p>
    </div>

    <div class="divider"></div>

    <ul class="contact-list">
      <li>
        <svg class="contact-icon" viewBox="0 0 20 20" aria-hidden="true">
          <rect width="20" height="20" fill="var(--ink)"/>
          <rect x="4" y="6" width="12" height="8" fill="none" stroke="var(--icon-ink)" stroke-width="1.5"/>
          <path d="M4 6 L10 11 L16 6" fill="none" stroke="var(--icon-ink)" stroke-width="1.5"/>
        </svg>
        info@hollanduw.com
      </li>
      <li>
        <svg class="contact-icon" viewBox="0 0 20 20" aria-hidden="true">
          <rect width="20" height="20" fill="var(--ink)"/>
          <circle cx="10" cy="10" r="6" fill="none" stroke="var(--icon-ink)" stroke-width="1.5"/>
          <path d="M4 10 H16 M10 4 C7 7 7 13 10 16 C13 13 13 7 10 4" fill="none" stroke="var(--icon-ink)" stroke-width="1.2"/>
        </svg>
        www.hollanduw.com
      </li>
      <li>
        <svg class="contact-icon" viewBox="0 0 20 20" aria-hidden="true">
          <rect width="20" height="20" fill="var(--ink)"/>
          <path d="M6 4 L8.5 4 L9.5 7.5 L8 8.5 C8.8 10.4 9.6 11.2 11.5 12 L12.5 10.5 L16 11.5 L16 14 C11 15 5 9 6 4 Z" fill="var(--icon-ink)"/>
        </svg>
        555-310-4821
      </li>
      <li>
        <svg class="contact-icon" viewBox="0 0 20 20" aria-hidden="true">
          <rect width="20" height="20" fill="var(--ink)"/>
          <rect x="6" y="3.5" width="8" height="13" rx="1.5" fill="none" stroke="var(--icon-ink)" stroke-width="1.5"/>
          <circle cx="10" cy="14" r="0.9" fill="var(--icon-ink)"/>
        </svg>
        555-310-7730
      </li>
      <li>
        <svg class="contact-icon" viewBox="0 0 20 20" aria-hidden="true">
          <rect width="20" height="20" fill="var(--ink)"/>
          <path d="M10 3.5 C7 3.5 5.5 5.8 5.5 8 C5.5 11 10 16.5 10 16.5 C10 16.5 14.5 11 14.5 8 C14.5 5.8 13 3.5 10 3.5 Z" fill="var(--icon-ink)"/>
          <circle cx="10" cy="8" r="1.8" fill="var(--ink)"/>
        </svg>
        1250 Harbor Rd, Bayview, CA. 90000
      </li>
    </ul>
  </main>
</body>
</html>
```